New Bicycle shop business card

Hi!
I'm looking for a business card for my new proffesional bike mechanics shop. This shop is only for fixing broken bikes and not selling bikes.
Peferbly a modern and sleek and modern design.
Colors: black, grey, red, white
Information:
Name: Rijwielwerkplaats Vanhoutte
Shop owner: Bart Vanhoutte & Marieke Segers
Website: www.rijwielwerkplaats-vanhoutte.be
Email: info@rijwielwerkplaats-vanhoutte.be
Phone number: +32471902368
Street adres: Kerkweg 46
9940 Bellebeke
Slogan/shop information: Herstellingen van alle merken.
Logo: see files.
Target Market(s)
People who seek a mechanic to fix or upgrade their bikes.
Contact Information for Business Card
Information:
Website: info@rijwielwerkplaats-vanhoutte.be
9940 Bellebeke
Logo: see files.

```html
<!DOCTYPE html>
<html lang="nl">
<head>
<meta charset="utf-8">
<title>Rijwielwerkplaats Vanhoutte – visitekaartje</title>
<link rel="stylesheet" href="https://fonts.googleapis.com/css2?family=Open+Sans:wght@400;600;700&display=swap">
<style>
  :root {
    --ink: #0a0a0b;
    --paper: #ffffff;
    --brand-red: #e8233f;
    --steel: #a7a9ac;
    --stage: #4a4c50;
    --card-w: 640px;
    --card-h: 366px;
  }
  * { box-sizing: border-box; margin: 0; padding: 0; }
  html, body { width: 1200px; height: 900px; overflow: hidden; }
  body {
    background: var(--stage);
    font-family: "Open Sans", Arial, sans-serif;
    position: relative;
  }
  .card {
    position: absolute;
    left: 280px;
    width: var(--card-w);
    height: var(--card-h);
    border-radius: 26px;
    overflow: hidden;
  }

  /* Back side */
  .card--back {
    top: 64px;
    background: var(--ink);
    color: var(--paper);
    display: flex;
    flex-direction: column;
    align-items: center;
    justify-content: center;
    gap: 14px;
  }
  .brand-mark {
    display: flex;
    align-items: center;
    gap: 14px;
  }
  .brand-dot {
    width: 34px; height: 34px;
    border-radius: 50%;
    background: var(--brand-red);
  }
  .brand-name {
    font-weight: 700;
    text-transform: uppercase;
    letter-spacing: 2px;
    font-size: 26px;
    line-height: 1.1;
    color: var(--paper);
  }
  .slogan {
    margin-top: 40px;
    font-size: 14px;
    letter-spacing: .3px;
  }

  /* Front side */
  .card--front {
    top: 470px;
    background: var(--ink);
  }
  .front-light {
    position: absolute; inset: 0;
    background: var(--paper);
    clip-path: polygon(0 0, 100% 0, 100% 36%, 0 47%);
  }
  .front-wordmark {
    position: absolute;
    top: 36px; right: 40px;
    font-weight: 700;
    text-transform: uppercase;
    letter-spacing: 1.5px;
    font-size: 20px;
    color: var(--ink);
  }
  .front-emblem-spot {
    position: absolute;
    right: 44px; top: 120px;
    width: 176px; height: 176px;
    border-radius: 50%;
    background: var(--brand-red);
    border: 5px solid var(--paper);
  }
  .owners {
    position: absolute;
    left: 48px; top: 66px;
    line-height: 1.35;
  }
  .owners__label { font-size: 21px; color: var(--ink); }
  .owners__names { font-size: 23px; color: var(--brand-red); }

  .contact {
    position: absolute;
    left: 48px; top: 184px;
    color: var(--paper);
  }
  .contact__company { color: var(--brand-red); font-weight: 700; font-size: 20px; line-height: 1.2; }
  .contact__role { font-weight: 600; font-size: 15px; line-height: 1.3; margin-bottom: 8px; }
  .contact__address { font-size: 13px; line-height: 1.35; margin-bottom: 8px; }
  .contact__list { list-style: none; font-size: 13px; line-height: 1.55; }
  .contact__list li { display: flex; align-items: center; gap: 10px; }
  .contact__list svg { width: 13px; height: 13px; fill: var(--brand-red); flex: none; }
</style>
</head>
<body>

  <section class="card card--back" aria-label="Achterkant">
    <div class="brand-mark">
      <span class="brand-dot"></span>
      <span class="brand-name">Rijwielwerkplaats Vanhoutte</span>
    </div>
    <p class="slogan">Herstellingen van alle merken.</p>
  </section>

  <section class="card card--front" aria-label="Voorkant">
    <div class="front-light"></div>
    <div class="front-wordmark">Rijwielwerkplaats Vanhoutte</div>
    <div class="front-emblem-spot"></div>

    <div class="owners">
      <p class="owners__label">Shop owner:</p>
      <p class="owners__names">Bart Vanhoutte &amp; Marieke Segers</p>
    </div>

    <div class="contact">
      <p class="contact__company">Rijwielwerkplaats Vanhoutte</p>
      <p class="contact__role">General Manager</p>
      <p class="contact__address">Kerkweg 46<br>9940 Bellebeke</p>
      <ul class="contact__list">
        <li>
          <svg viewBox="0 0 24 24" aria-hidden="true"><path d="M6.6 10.8a15.1 15.1 0 0 0 6.6 6.6l2.2-2.2a1 1 0 0 1 1-.25 11.4 11.4 0 0 0 3.6.57 1 1 0 0 1 1 1V20a1 1 0 0 1-1 1A17 17 0 0 1 3 4a1 1 0 0 1 1-1h3.5a1 1 0 0 1 1 1c0 1.25.2 2.45.57 3.57a1 1 0 0 1-.25 1z"/></svg>
          +32471902368
        </li>
        <li>
          <svg viewBox="0 0 24 24" aria-hidden="true"><path d="M2 5h20v14H2zm2 2v.5l8 5 8-5V7zm0 2.8V17h16V9.8l-8 5z"/></svg>
          info@rijwielwerkplaats-vanhoutte.be
        </li>
        <li>
          <svg viewBox="0 0 24 24" aria-hidden="true"><circle cx="12" cy="12" r="10"/></svg>
          www.rijwielwerkplaats-vanhoutte.be
        </li>
      </ul>
    </div>
  </section>

</body>
</html>
```